New Company Business Card design

Looking for a corporate looking business card utilising my new logo design - the logo i would like embossed as one option and flat as another - simplistic but stylish - less is more - we are an import export business launching into the market - i would like a couple of options as main background - Grey or Black

```html
<!DOCTYPE html>
<html lang="en">
<head>
<meta charset="utf-8">
<title>Meridian Trade Partners – Business Card</title>
<link href="https://fonts.googleapis.com/css2?family=Roboto:wght@400;500&display=swap" rel="stylesheet">
<style>
  :root {
    --backdrop: #e8e5e0;
    --card-light: #f4f4f3;
    --card-dark: #1b1c1e;
    --brand-blue: #1a78c2;
    --text-grey: #5a5a5a;
    --text-dark: #3a3a3a;
    --rule-grey: #8a8a8a;
    --text-white: #f2f2f2;
  }
  * { margin: 0; padding: 0; box-sizing: border-box; }
  html, body {
    width: 1200px; height: 960px; overflow: hidden;
    background: var(--backdrop);
    font-family: "Roboto", Arial, sans-serif;
  }
  .canvas { position: relative; width: 1200px; height: 960px; }

  .card {
    position: absolute; width: 600px; height: 343px; overflow: hidden;
    box-shadow: 0 3px 8px rgba(0,0,0,0.18);
  }
  .card--front { left: 314px; top: 113px; background: var(--card-light); }
  .card--back { left: 311px; top: 472px; background: var(--card-dark); }

  .brand {
    position: absolute; display: flex; align-items: center; gap: 10px;
    font-weight: 500; color: var(--brand-blue); white-space: nowrap;
  }
  .brand__dot { width: 18px; height: 18px; border-radius: 50%; background: var(--brand-blue); flex: none; }
  .card--front .brand { right: 28px; top: 100px; font-size: 20px; letter-spacing: 0.5px; }
  .card--back .brand { left: 0; right: 0; top: 130px; justify-content: center; font-size: 30px; letter-spacing: 1px; }
  .card--back .brand__dot { width: 26px; height: 26px; }

  .edge-tab {
    position: absolute; left: -16px; top: 187px; width: 27px; height: 32px;
    border-radius: 50%; background: var(--brand-blue);
  }
  .holder { position: absolute; left: 29px; top: 184px; }
  .holder__name { font-size: 22px; font-weight: 500; color: var(--brand-blue); line-height: 1.1; }
  .holder__title { font-size: 15px; color: var(--text-grey); margin-top: 3px; }
  .divider { position: absolute; left: 29px; right: 29px; top: 233px; height: 1px; background: var(--rule-grey); }

  .contact-list { position: absolute; left: 29px; top: 244px; list-style: none; }
  .contact-list li {
    display: flex; align-items: center; gap: 9px; height: 19px;
    font-size: 14.5px; color: var(--text-dark);
  }
  .contact-list svg { width: 14px; height: 14px; fill: var(--brand-blue); flex: none; }

  .address {
    position: absolute; right: 27px; top: 265px; text-align: right;
    font-size: 14.5px; line-height: 19px; color: var(--text-dark); font-style: normal;
  }
  .address__web { font-weight: 500; }

  .back-web {
    position: absolute; left: 0; right: 0; top: 289px; text-align: center;
    font-size: 14px; letter-spacing: 1.6px; color: var(--text-white);
  }
</style>
</head>
<body>
<main class="canvas">
  <section class="card card--front" aria-label="Card front">
    <div class="brand"><span class="brand__dot"></span>Meridian Trade Partners</div>
    <span class="edge-tab"></span>
    <div class="holder">
      <p class="holder__name">DANIEL REYES</p>
      <p class="holder__title">CEO/FOUNDER</p>
    </div>
    <div class="divider"></div>
    <ul class="contact-list">
      <li><svg viewBox="0 0 24 24"><path d="M6.6 10.8a15 15 0 006.6 6.6l2.2-2.2a1 1 0 011-.25 11.4 11.4 0 003.6.57 1 1 0 011 1V20a1 1 0 01-1 1A17 17 0 013 4a1 1 0 011-1h3.5a1 1 0 011 1c0 1.25.2 2.45.57 3.57a1 1 0 01-.25 1z"/></svg>555 214 7390</li>
      <li><svg viewBox="0 0 24 24"><path d="M7 1h10a2 2 0 012 2v18a2 2 0 01-2 2H7a2 2 0 01-2-2V3a2 2 0 012-2zm0 3v14h10V4zm5 15.5a1 1 0 100 2 1 1 0 000-2z"/></svg>555 381 6027</li>
      <li><svg viewBox="0 0 24 24"><path d="M6 2h12v6H6zM3 9h18a1 1 0 011 1v8h-4v4H6v-4H2v-8a1 1 0 011-1zm5 8v3h8v-3z"/></svg>555 749 1186</li>
      <li><svg viewBox="0 0 24 24"><path d="M2 5h20v14H2zm2 2v.5l8 5 8-5V7zm0 2.8V17h16V9.8l-8 5z"/></svg>daniel@meridiantp.com</li>
    </ul>
    <address class="address">
      1420 Harbor View Road<br>
      Juneau, Alaska 99801<br>
      <span class="address__web">www.meridiantp.com</span>
    </address>
  </section>

  <section class="card card--back" aria-label="Card back">
    <div class="brand"><span class="brand__dot"></span>Meridian Trade Partners</div>
    <p class="back-web">www.meridiantradepartners.com</p>
  </section>
</main>
</body>
</html>
```